Wordpress Design Project

Hi,

I would like a more modern colourful design doing for my website ZAP Lnx (www.za%plnx.com - remove percentage). But I do still want to keep the same sort of colors, just maybe lighter. More interesting.

I want the inside pages to NOT all look the same with just boring text.

I want the site to look more appealing and maybe a new logo.
Updates

I would like to mention I would prefer to keep the same logo after rethinking it (possibly a slight refresh of the logo if you feel its a good idea) and the same color scheme as at present.

Saves us rebranding a lot of our apps, tools online ads etc.

Also I thought it is worth mentioning we have 2 parts to the site. The front end and the logged in area. It would be good if when making the front end you keep in mind the back end at http://p.za%plnx.com (remove percentage). We can only edit this limitedly (can edit the entire footer, the logo and full CSS of it). Would be good if we could make sure the header and footer can be used on the back end as well maybe to make it match.

I also want layouts making not just for the homepage. Obviously every page will basically be the same but I don't want all the other pages to just be 'text' and no real layout.

You can see out main pages on the website at the moment, I want those other pages to be laid out nice and differently as well. For example the testimonials page could be more interesting with speech bubbles and pictures of each person (just use placeholders). The affiliates page could be a description and then a nice fancy list of features why to join etc. 

Nothing overly complicated but I think it makes the whole site seem a lot better.

Target Market(s)

Affiliate Marketing. International.

Requirements
Must have
• Needs to be more room for links across the navigation at the top, also sub menus (at present we have a lot of pages which are hidden deep within other pages).
Nice to have
• Lists of features for advertisers and affiliates on the homepage part.

Menu items and buttons have nice hover over effects.

I want to get across on our pages all the different unique features we have.

Maybe some kind of slider which has past offer logos in, just use example logos.

```html
<!DOCTYPE html>
<html lang="en">
<head>
<meta charset="utf-8">
<title>ZAP Lnx – Earn Money &amp; Increase Sales</title>
<link rel="stylesheet" href="https://fonts.googleapis.com/css2?family=Arimo:wght@400;700&display=swap">
<style>
:root{
  --brand-blue:#1f6fae;
  --brand-blue-dark:#0d4f86;
  --brand-blue-light:#6fb0de;
  --accent-orange:#f7941d;
  --accent-orange-light:#fbb040;
  --ink:#222;
  --ink-soft:#444;
  --link:#0d4f86;
  --panel-gray:#eeeeee;
  --footer-dark:#1d1d1d;
  --footer-gray:#4a4a4a;
  --white:#fff;
}
*{box-sizing:border-box;margin:0;padding:0}
html,body{width:1018px;height:1200px;overflow:hidden}
body{
  font-family:"Arimo",Arial,sans-serif;color:var(--ink);position:relative;
  background:linear-gradient(to bottom,#fff 0,#fff 150px,#c9ccd0 160px,#aeb3b9 470px,#7fb8e2 500px,#5ea2d6 760px,#1f6fae 1000px,#1f6fae 1080px);
}
.top-strip{position:absolute;left:0;top:0;width:1018px;height:5px;background:var(--brand-blue-dark)}
.abs{position:absolute}

/* header */
.brand{left:155px;top:30px}
.brand-name{font-size:60px;font-weight:700;color:var(--brand-blue);letter-spacing:1px;line-height:1;display:flex;align-items:center;gap:12px}
.brand-dot{width:22px;height:22px;border-radius:50%;background:var(--accent-orange)}
.brand-tagline{font-size:17px;font-weight:700;color:var(--brand-blue);margin-top:6px;letter-spacing:.3px}
.call-bubble{left:650px;top:14px;width:162px;height:40px;background:var(--accent-orange-light);border-radius:4px;padding:3px 12px;color:var(--white)}
.call-bubble b{display:block;font-size:17px;line-height:18px}
.call-bubble span{font-size:13px}
.call-bubble::after{content:"";position:absolute;left:90px;bottom:-10px;border:6px solid transparent;border-top:6px solid var(--accent-orange-light)}
.contact{left:652px;top:66px;font-size:12px;color:var(--ink-soft);line-height:15px}
.contact .tel{font-size:17px;font-weight:700;color:var(--ink);margin-bottom:3px}

/* nav */
.main-nav{left:137px;top:123px;width:744px;height:34px;display:flex;background:linear-gradient(#2f84c4,#14609f);border:1px solid #0d4f86}
.main-nav a{flex:1 1 auto;color:var(--white);font-size:13px;text-decoration:none;display:flex;align-items:center;justify-content:center;border-right:1px solid rgba(255,255,255,.25)}
.main-nav a:last-child{border-right:0}
.main-nav a.active{background:var(--accent-orange-light);flex:0 0 72px}
.hover-note{left:365px;top:159px;font-size:8px;color:#555}

/* content sheet */
.sheet{left:137px;top:157px;width:744px;height:909px;background:var(--white)}

/* slider */
.slider{left:141px;top:167px;width:734px;height:300px;background:#e4e6e8;border-radius:4px;box-shadow:0 3px 6px rgba(0,0,0,.2)}
.slide{left:152px;top:172px;width:712px;height:283px;background:linear-gradient(to bottom,#3a8bcb,#1a5f9c 55%,#3b86c1 70%,#155a95)}
.slide-title{left:171px;top:182px;font-size:35px;color:var(--white)}
.slide-text{left:199px;top:265px;width:360px;font-size:17px;line-height:19px;color:#e8f1fa}
.btn{background:linear-gradient(var(--accent-orange-light),var(--accent-orange));color:var(--white);font-size:12px;border-radius:3px;text-align:center}
.slide-btn{left:421px;top:338px;width:90px;height:26px;line-height:26px}
.slide-cta{left:199px;top:387px;width:340px;font-size:24px;color:var(--white);line-height:30px;text-align:right}
.slide-cta span{display:block;text-align:left}
.slide-art{left:556px;top:184px;width:280px;height:244px;background:linear-gradient(135deg,#9cc6ea,#2b6ea8 60%,#4c6b3a);border-radius:4px}
.slider-arrow{top:288px;width:46px;height:46px;border-radius:50%;background:linear-gradient(#fff,#d8d8d8);box-shadow:0 1px 3px rgba(0,0,0,.4)}
.slider-arrow svg{position:absolute;left:14px;top:13px}
.slider-dots{left:489px;top:472px;width:44px;height:12px;display:flex;gap:3px}
.slider-dots i{width:8px;height:8px;border-radius:50%;background:#aaa}
.slider-dots i:first-child{background:var(--accent-orange)}

/* feature panels */
.feature-panel{top:501px;width:311px;height:190px}
.feature-panel.left{left:124px}
.feature-panel.right{left:583px}
.feature-list{top:526px;width:190px;list-style:none;font-size:12px;line-height:18px;color:var(--ink)}
.feature-list li::before{content:"";display:inline-block;margin-right:8px;border:4px solid transparent;border-left:6px solid var(--accent-orange)}
.feature-badge{top:514px;width:162px;height:162px;border-radius:50%;background:radial-gradient(circle at 50% 35%,#3f98da,#1562a3 70%);border:6px solid #e6edf4;box-shadow:0 3px 6px rgba(0,0,0,.3);color:var(--white);font-size:21px;font-weight:700;display:flex;align-items:center;justify-content:center}
.signup{top:640px;width:80px;height:24px;line-height:24px}

/* welcome */
.welcome-title{left:160px;top:766px;font-size:18px;color:var(--ink)}
.welcome-title b{font-weight:400;color:var(--brand-blue)}
.welcome-text{left:160px;top:806px;width:455px;font-size:10px;line-height:13px;color:var(--ink-soft)}
.read-more{left:515px;top:902px;width:80px;height:22px;line-height:22px;font-size:11px;color:var(--white);border-radius:3px;text-align:center;background:linear-gradient(#2f84c4,#14609f)}
.divider{left:141px;top:956px;width:474px;height:1px;background:#ccc}

/* partners */
.partners{left:141px;top:990px;width:474px;height:44px;display:flex;align-items:center;justify-content:space-between}
.partner{height:30px;background:#bdbdbd;border-radius:4px}
.partner.round{width:30px;border-radius:50%}

/* side panels */
.side-panel{left:631px;width:250px;background:var(--panel-gray)}
.side-head{left:631px;width:261px;height:34px;background:linear-gradient(#2f84c4,#14609f);color:var(--white);font-size:14px;padding:9px 0 0 33px}
.side-head i{position:absolute;right:14px;top:8px;width:19px;height:19px;border-radius:50%;background:#0a3d69;border:1px solid #fff}
.side-head i::after{content:"";position:absolute;left:5px;top:7px;border:4px solid transparent;border-top:4px solid #fff}
.login-label{left:646px;font-size:11px}
.login-input{left:703px;width:165px;height:24px;background:var(--white);border:1px solid #c8c8c8}
.side-link{left:646px;font-size:11px;color:var(--link);text-decoration:underline}
.login-btn{left:788px;top:867px;width:80px;height:24px;line-height:24px;font-size:12px}
.follow{left:771px;top:1004px;font-size:10px;color:#555}
.social{top:1018px;width:30px;height:32px;border-radius:5px}

/* footer */
.footer-links{left:0;top:1083px;width:1018px;height:26px;background:var(--footer-dark);display:flex;justify-content:center;align-items:center;gap:20px;font-size:11px;color:var(--white)}
.footer-base{left:0;top:1109px;width:1018px;height:91px;background:linear-gradient(#3a3a3a,#5a5a5a)}
.app-tray{left:215px;top:1113px;width:590px;height:62px}
.apps{left:290px;top:1128px;display:flex;gap:28px}
.app{display:flex;align-items:center;gap:6px}
.app-icon{width:20px;height:24px;border-radius:4px}
.app b{display:block;font-size:9px;color:var(--brand-blue-dark)}
.app small{display:block;font-size:6px;color:#666}
.copyright{left:365px;top:1173px;width:289px;height:20px;background:#1a1a1a;border-radius:3px;color:var(--white);font-size:10px;text-align:center;line-height:20px}
</style>
</head>
<body>
<div class="top-strip"></div>

<header>
  <div class="abs brand">
    <div class="brand-name">ZAP Lnx <span class="brand-dot"></span></div>
    <div class="brand-tagline">EARN MONEY &amp; INCREASE SALES</div>
  </div>
  <div class="abs call-bubble"><b>Any questions?</b><span>Call Us &nbsp;&nbsp;&nbsp; :</span></div>
  <div class="abs contact">
    <div class="tel">Telp &nbsp;:+44 (0)1000 - 555014</div>
    Fax &nbsp;&nbsp;&nbsp;&nbsp;: +44 (0)1000 - 5550178<br>
    Email &nbsp;: info@zaplnx.com
  </div>
  <nav class="abs main-nav">
    <a href="#">HOME</a><a href="#">ABOUT US</a><a href="#" class="active">BLOG</a><a href="#">TESTIMONIALS</a><a href="#">AFFILIATES</a><a href="#">ADVERTISERS</a><a href="#">CONTACT US</a>
  </nav>
</header>

<div class="abs sheet"></div>
<div class="abs hover-note">mouse over effect</div>

<section>
  <div class="abs slider"></div>
  <div class="abs slide"></div>
  <div class="abs slide-art" role="img" aria-label="Hand offering banknotes out of a computer monitor"></div>
  <div class="abs slide-title">Monetize Your Site Traffic</div>
  <p class="abs slide-text">Lorem ipsum dolor sit amet, consecteteur adipiscing elit. set diem nonumy nibh eusmod tincidunt ut laoret dolor magna aliquam.....</p>
  <div class="abs btn slide-btn">Read More</div>
  <div class="abs slide-cta"><span>International Affiliate Network</span>Join Us today!</div>
  <div class="abs slider-arrow" style="left:134px"><svg width="16" height="20"><path d="M12 2 4 10l8 8" fill="none" stroke="#444" stroke-width="4"/></svg></div>
  <div class="abs slider-arrow" style="left:836px"><svg width="16" height="20"><path d="M4 2l8 8-8 8" fill="none" stroke="#444" stroke-width="4"/></svg></div>
  <div class="abs slider-dots"><i></i><i></i><i></i><i></i></div>
</section>

<section>
  <svg class="abs feature-panel left" viewBox="0 0 311 190">
    <path d="M0 0H260l20 20V170l-20 20H20L6 175Z" fill="#1f6fae"/>
    <rect x="28" y="24" width="250" height="148" rx="4" fill="#fff"/>
  </svg>
  <svg class="abs feature-panel right" viewBox="0 0 311 190">
    <path d="M311 0H51L31 20V170l20 20H291l14-15Z" fill="#1f6fae"/>
    <rect x="33" y="24" width="250" height="148" rx="4" fill="#fff"/>
  </svg>
  <ul class="abs feature-list" style="left:164px"><li>Lorem ipsum dolor sit amet.</li><li>Lorem ipsum dolor sit amet.</li><li>Lorem ipsum dolor sit amet.</li><li>Lorem ipsum dolor sit amet.</li><li>Lorem ipsum dolor sit amet.</li></ul>
  <ul class="abs feature-list" style="left:686px"><li>Lorem ipsum dolor sit amet.</li><li>Lorem ipsum dolor sit amet.</li><li>Lorem ipsum dolor sit amet.</li><li>Lorem ipsum dolor sit amet.</li><li>Lorem ipsum dolor sit amet.</li></ul>
  <div class="abs feature-badge" style="left:344px">ADVERTISER</div>
  <div class="abs feature-badge" style="left:512px">AFFILIATE</div>
  <div class="abs btn signup" style="left:253px">Sign Up Now!</div>
  <div class="abs btn signup" style="left:686px">Sign Up Now!</div>
</section>

<main>
  <h1 class="abs welcome-title">Welcome to <b>ZAP Lnx.com</b></h1>
  <p class="abs welcome-text">Lorem ipsum dolor sit amet, consectetuer adipiscing elit. set diem nonumy nibh euismod tincidunt ut laoreet dolor magna aliquam erat volutpat. ut wisi enim ad minim veniam. Nemo enim ipsam voluptatem quia voluptas sit aspernatur aut odit aut fugit, set quia consequuntur.<br>Lorem ipsum dolor sit amet, consectetuer adipiscing elit. set diem nonumy nibh euismod tincidunt ut laoreet dolor magna aliquam erat volutpat. ut wisi enim ad minim veniam. nemo enim ipsam voluptatem quia voluptas sit aspernatur aut odit aut fugit, set quia consequuntur.</p>
  <div class="abs read-more">Read more</div>
  <div class="abs divider"></div>
  <div class="abs partners">
    <svg width="12" height="16"><path d="M10 0 0 8l10 8Z" fill="#999"/></svg>
    <span class="partner" style="width:34px"></span>
    <span class="partner round"></span>
    <span class="partner" style="width:80px"></span>
    <span class="partner" style="width:40px"></span>
    <span class="partner" style="width:76px"></span>
    <span class="partner" style="width:90px"></span>
    <svg width="12" height="16"><path d="M2 0l10 8-10 8Z" fill="#999"/></svg>
  </div>
</main>

<aside>
  <div class="abs side-panel" style="top:737px;height:205px"></div>
  <div class="abs side-head" style="top:747px">MEMBERS AREA<i></i></div>
  <div class="abs login-label" style="top:810px">Email</div>
  <div class="abs login-input" style="top:803px"></div>
  <div class="abs login-label" style="top:841px">Password</div>
  <div class="abs login-input" style="top:835px"></div>
  <div class="abs side-link" style="top:872px">Forgot Your Password?</div>
  <div class="abs btn login-btn">LOGIN</div>
  <div class="abs side-link" style="top:902px">New User ? Register here</div>

  <div class="abs side-panel" style="top:960px;height:106px"></div>
  <div class="abs side-head" style="top:965px">Recent Blog Posts<i></i></div>
  <div class="abs side-link" style="top:1010px">New Offers</div>
  <div class="abs side-link" style="top:1026px">New Offers</div>
  <div class="abs side-link" style="top:1042px">New Offers</div>
  <div class="abs follow">FOLLOW US ON :</div>
  <span class="abs social" style="left:765px;background:#5fb4e6"></span>
  <span class="abs social" style="left:801px;background:#c9302c"></span>
  <span class="abs social" style="left:837px;background:#3b5b9a"></span>
</aside>

<footer>
  <nav class="abs footer-links"><span>Affiliate</span><span>About Us</span><span>Terms &amp; Conditions</span><span>Advertiser</span><span>Blogs</span><span>Privacy Policy &amp; Cookies</span><span>FAQ's</span><span>Contact Us</span></nav>
  <div class="abs footer-base"></div>
  <svg class="abs app-tray" viewBox="0 0 590 62"><path d="M0 0H590C560 0 560 62 530 62H60C30 62 30 0 0 0Z" fill="#f2f2f2"/></svg>
  <div class="abs apps">
    <div class="app"><span class="app-icon" style="background:#2a5d9a"></span><div><b>Mobile Stats</b><small>ZAP Lnx Mobile Website</small></div></div>
    <div class="app"><span class="app-icon" style="background:#d9a321;border-radius:50%"></span><div><b>Orbit Browser</b><small>Official ZAP Lnx Extension</small></div></div>
    <div class="app"><span class="app-icon" style="background:#e0722a;border-radius:50%"></span><div><b>Ember Browser</b><small>Official ZAP Lnx Extension</small></div></div>
    <div class="app"><span class="app-icon" style="background:#8fbf3f"></span><div><b>Droidline App</b><small>Official ZAP Lnx App</small></div></div>
  </div>
  <div class="abs copyright">Copyright © 2013, zaplnx.com. All rights reserved.</div>
</footer>
</body>
</html>
```